Personalized Technology Company Needs a Business Card

I need a double-sided business card. Both sides will have the logo, and the contact information. One side will be black, with the white / gray logo, and the other will be white, with the black / gray logo. The black side will have the text "Custom Gaming PC's" and will have a water-cooled gaming PC image. The white side will have the text "Custom Business Computers & Consulting", and will have a business / enterprise PC image. Feel free to add a conservative image in the background, while the color remains unchanged. I'm uploading the base logo (transparent), so you can modify the colors, both the finished colored logos and an idea of ​​the business card (with the current information, just missing the website, which is www.velomindsystems.com, please add it.) Thank you so much for your effort, I'll be specting your cool designs. Good Luck!

Target Market(s)

Gamers & Entrepreneurs / Business Owners / Chief Technology Officers

Industry/Entity Type

Technology Equipment

Contact Information for Business Card

I need a double-sided business card. Both sides will have the logo, and the contact information. One side will be black, with the white/gray logo, and the other one will be white, with the black/gray logo. The black side will have the text "Custom Gaming PC's" and will have a water-cooled gaming PC image. The white side will have the text "Custom Business Computers & Consulting", and will have a business/enterprise PC image. Feel free to add a conservative image in the background, whilst the color remains unchanged.

I'm uploading the base logo (transparent), so you can modify the colors, both the finished colored logos and an idea of the business card (with the actual information, just missing the website, which is www.velomindsystems.com, please add it.)

Thank you so much for your effort, I'll be specting your cool designs. Good Luck!

Font styles to use
Serif

Colors
000000
757575
ffffff

Requirements
Must have
• Please See Description
Nice to have
• Please See Description
Should not have
• Please See Description

```html
<!DOCTYPE html>
<html lang="en">
<head>
<meta charset="utf-8">
<title>Velomind Systems – Business Cards</title>
<link rel="stylesheet" href="https://fonts.googleapis.com/css2?family=Archivo:wght@400;500;600;800;900&family=Roboto+Condensed:wght@300;400&display=swap">
<style>
  :root {
    --black: #000000;
    --grey: #757575;
    --white: #ffffff;
    --sand: #bcac9b;
    --cream: #ece6dc;
    --page: #e4e4e4;
    --violet-deep: #1a1440;
    --violet: #5a4bb8;
    --violet-glow: #b7a6ff;
  }
  * { margin: 0; padding: 0; box-sizing: border-box; }
  html, body { width: 1200px; height: 1200px; overflow: hidden; }
  body {
    background: var(--page);
    font-family: "Archivo", Arial, sans-serif;
    position: relative;
  }
  .card {
    position: absolute;
    left: 199px;
    width: 840px;
    height: 482px;
    overflow: hidden;
  }
  .card--light { top: 78px; background: var(--white); color: var(--black); }
  .card--dark { top: 639px; background: var(--black); color: var(--white); }

  .card__panel { position: absolute; inset: 0; width: 100%; height: 100%; }

  .card__visual {
    position: absolute;
    left: 29px; top: 86px;
    width: 240px; height: 164px;
    background: linear-gradient(135deg, #3a3a3a 0%, #8c8c8c 45%, #e08a2c 60%, #c9c9c9 100%);
    border-radius: 4px;
    opacity: .85;
  }

  .tagline { position: absolute; left: 33px; top: 262px; line-height: 1; }
  .tagline__lead {
    font-weight: 800; font-size: 31px; letter-spacing: 14px; display: block;
  }
  .tagline__main {
    font-weight: 900; font-size: 60px; letter-spacing: -1px; display: block; margin-top: 4px;
  }
  .tagline__sub {
    font-weight: 800; font-size: 32px; display: block; margin-top: 7px;
  }
  .card--dark .tagline { left: 45px; top: 231px; color: var(--cream); }
  .card--dark .tagline__main { font-size: 58px; margin-top: 6px; }
  .card--dark .tagline__sub { font-size: 34px; }

  .brand {
    position: absolute;
    right: 40px; top: 118px;
    display: flex; align-items: center; gap: 14px;
  }
  .brand__mark { width: 34px; height: 34px; background: var(--grey); }
  .card--dark .brand__mark { background: var(--sand); }
  .brand__name {
    font-weight: 600; font-size: 30px; letter-spacing: 4px; white-space: nowrap;
  }

  .contact {
    position: absolute; right: 35px; top: 228px; text-align: right;
  }
  .contact__name { font-weight: 500; font-size: 34px; letter-spacing: -.5px; line-height: 1; }
  .contact__role { font-weight: 400; font-size: 21px; margin-top: 6px; }
  .contact__phones { margin-top: 26px; font-weight: 400; font-size: 25px; line-height: 1.3; }
  .contact__email {
    font-family: "Roboto Condensed", Arial, sans-serif;
    font-weight: 300; font-size: 23px; margin-top: 16px;
  }
</style>
</head>
<body>

<section class="card card--light">
  <svg class="card__panel" viewBox="0 0 840 482" preserveAspectRatio="none" aria-hidden="true">
    <polygon points="0,0 253,0 518,482 0,482" fill="var(--sand)"/>
    <polygon points="262,0 269,0 522,482 517,482" fill="var(--sand)"/>
  </svg>
  <div class="card__visual" role="img" aria-label="Business desktop computer, monitor and laptop"></div>
  <h2 class="tagline">
    <span class="tagline__lead">CUSTOM</span>
    <span class="tagline__main">BUSINESS</span>
    <span class="tagline__sub">COMPUTERS</span>
    <span class="tagline__sub">&amp; CONSULTING</span>
  </h2>
  <div class="brand">
    <span class="brand__mark"></span>
    <span class="brand__name">VELOMIND SYSTEMS</span>
  </div>
  <div class="contact">
    <p class="contact__name">MARCO RUIZ DELGADO</p>
    <p class="contact__role">CEO &amp; CO-FOUNDER</p>
    <p class="contact__phones">+52 5123 - 4567<br>+52 55 - 1234 - 5678</p>
    <p class="contact__email">contact@velomindsystems.com</p>
  </div>
</section>

<section class="card card--dark">
  <svg class="card__panel" viewBox="0 0 840 482" preserveAspectRatio="none" role="img" aria-label="Water-cooled gaming PC interior with violet lighting">
    <defs>
      <linearGradient id="rig-glow" x1="0" y1="0" x2="1" y2="1">
        <stop offset="0" stop-color="var(--violet)"/>
        <stop offset=".45" stop-color="var(--violet-deep)"/>
        <stop offset=".75" stop-color="var(--violet)"/>
        <stop offset="1" stop-color="var(--violet-glow)"/>
      </linearGradient>
    </defs>
    <polygon points="0,0 253,0 518,482 0,482" fill="url(#rig-glow)" opacity=".8"/>
    <polygon points="253,0 262,0 522,482 517,482" fill="var(--white)"/>
  </svg>
  <h2 class="tagline">
    <span class="tagline__lead">CUSTOM</span>
    <span class="tagline__main">GAMING</span>
    <span class="tagline__sub">PC'S</span>
  </h2>
  <div class="brand">
    <span class="brand__mark"></span>
    <span class="brand__name">VELOMIND SYSTEMS</span>
  </div>
  <div class="contact">
    <p class="contact__name">MARCO RUIZ DELGADO</p>
    <p class="contact__role">CEO &amp; CO-FOUNDER</p>
    <p class="contact__phones">+52 5123 - 4567<br>+52 55 - 1234 - 5678</p>
    <p class="contact__email">contact@velomindsystems.com</p>
  </div>
</section>

</body>
</html>
```